Erstellung eines Polizeiwimpels für Kinder
Zielgruppe
Wir stellen Fahrradwimpel für Kinder her. Hier finden Sie unsere Produkte: https://www.kaufhalle-wiro.de/laden/regal/58203917462
Aufgabenstellung
Wir möchten einen 'Polizeiwimpel' für Kinder herstellen.
Wenn möglich, nur eine Farbe verwenden (reduziert Kosten in der Produktion). Der Hintergrund soll 'Polizei Blau' sein.
Wimpelgröße: 17,5 cm X 32 cm X 32cm (Dreieckig)
Ich habe ein selbst erstelltes Design hochgeladen. Es soll den Schriftzug 'Polizei' enthalten und evtl. noch 'Polizei Symbole', die Jungs (und ihre Eltern) ansprechen. (Pistole, Sheriffstern, etc.) Das offizielle Wappen oder andere Hoheitssymbole dürfen wir allerdings nicht verwenden.

```html
<!DOCTYPE html>
<html lang="de">
<head>
<meta charset="utf-8">
<title>Polizeiwimpel</title>
<link rel="stylesheet" href="https://fonts.googleapis.com/css2?family=Open+Sans:wght@400;700&display=swap">
<style>
  :root {
    --paper: #ffffff;
    --police-blue: #1671b8;
    --stripe-grey: #dcdcdc;
    --icon-tone: #8fb3d6;
  }
  html, body {
    margin: 0;
    padding: 0;
    width: 1200px;
    height: 657px;
    overflow: hidden;
    background: var(--paper);
  }
  .pennant {
    display: block;
    width: 1200px;
    height: 657px;
  }
  .pennant__field { fill: var(--police-blue); }
  .pennant__border {
    fill: none;
    stroke: var(--stripe-grey);
    stroke-width: 24;
    stroke-dasharray: 60 33;
  }
  .pennant__siren { fill: var(--icon-tone); }
  .pennant__title {
    font-family: "Open Sans", Arial, sans-serif;
    font-weight: 700;
    font-size: 172px;
    fill: var(--stripe-grey);
  }
  .pennant__web {
    font-family: "Open Sans", Arial, sans-serif;
    font-weight: 400;
    font-size: 14px;
    fill: var(--stripe-grey);
  }
</style>
</head>
<body>
<svg class="pennant" viewBox="0 0 1200 657" xmlns="http://www.w3.org/2000/svg">
  <polygon class="pennant__field" points="0,0 1197,326 0,657"/>

  <line class="pennant__border" x1="0" y1="46" x2="1050" y2="314"/>
  <line class="pennant__border" x1="0" y1="614" x2="1050" y2="350"/>

  <rect class="pennant__siren" x="80" y="165" width="190" height="205" rx="14"
        role="img" aria-label="Blaulicht-Symbol mit Lichtstrahlen"/>

  <text class="pennant__title" x="46" y="552" textLength="690" lengthAdjust="spacing"
        transform="rotate(-14 46 552)">POLIZEI</text>

  <text class="pennant__web" x="752" y="380" transform="rotate(-14 752 380)">www.rollradl.bike</text>
</svg>
</body>
</html>
```